Maple Grove Schools | brand new stationery!

We need stationery design with our new logo! Our company updated it's name and image and we like to incorporate the new one on our stationery, business cards and email signature. We are looking for fresh, new ideas!
Industry: Childcare, Elementary and Middle School
Company Name: Maple Grove Schools
Tagline: Growing Curious Minds Daily
Main colors: Blue, white and a little yellow
Star shape is something new for us! Do you see a way to incorporate it as a design element?

```html
<!DOCTYPE html>
<html lang="en">
<head>
<meta charset="utf-8">
<title>Maple Grove Schools – Email Signature</title>
<link rel="stylesheet" href="https://fonts.googleapis.com/css2?family=Raleway:wght@500;600;700&family=Roboto:wght@400;500&display=swap">
<style>
  :root {
    --page: #e6e7e9;
    --card: #ffffff;
    --navy: #2b2d6e;
    --ink: #1e1f33;
    --gold: #f5c211;
    --text: #6a6a6a;
    --photo-a: #c9b8ab;
    --photo-b: #6e4a3a;
  }
  * { box-sizing: border-box; margin: 0; padding: 0; }
  html, body { width: 1200px; height: 1200px; overflow: hidden; }
  body {
    background: var(--page);
    position: relative;
    font-family: "Roboto", Arial, sans-serif;
  }
  .showcase-title {
    position: absolute;
    top: 240px;
    left: 0;
    width: 1200px;
    text-align: center;
    font-family: "Raleway", Arial, sans-serif;
    font-size: 34px;
    font-weight: 500;
    color: var(--navy);
    letter-spacing: 0.5px;
  }
  .showcase-title strong { font-weight: 700; }
  .signature {
    position: absolute;
    left: 259px;
    width: 682px;
    background: var(--card);
    box-shadow: 7px 7px 7px rgba(0, 0, 0, 0.45);
  }
  .signature--photo { top: 346px; height: 238px; }
  .signature--logo { top: 618px; height: 236px; }

  .portrait {
    position: absolute;
    left: 85px;
    top: 52px;
    width: 150px;
    height: 131px;
    clip-path: polygon(25% 0, 75% 0, 100% 50%, 75% 100%, 25% 100%, 0 50%);
    background: radial-gradient(ellipse at 50% 40%, var(--photo-a) 0%, #a27f6b 45%, var(--photo-b) 100%);
  }

  .brand-block {
    position: absolute;
    left: 63px;
    top: 48px;
    width: 180px;
    text-align: center;
  }
  .brand-dot {
    width: 40px;
    height: 40px;
    border-radius: 50%;
    background: var(--navy);
    margin: 0 auto 12px;
  }
  .brand-name {
    font-family: "Raleway", Arial, sans-serif;
    font-weight: 700;
    font-size: 26px;
    line-height: 27px;
    color: var(--ink);
  }
  .brand-tagline {
    margin-top: 7px;
    font-size: 10px;
    letter-spacing: 1.2px;
    color: var(--navy);
  }

  .divider {
    position: absolute;
    width: 1.5px;
    background: var(--gold);
  }
  .signature--photo .divider { left: 269px; top: 44px; height: 146px; }
  .signature--logo .divider { left: 262px; top: 43px; height: 148px; }

  .details { position: absolute; }
  .signature--photo .details { left: 294px; top: 46px; }
  .signature--logo .details { left: 295px; top: 46px; }

  .person-name {
    font-family: "Raleway", Arial, sans-serif;
    font-weight: 700;
    font-size: 17.5px;
    color: var(--navy);
    letter-spacing: 0.3px;
  }
  .person-role {
    font-size: 14.5px;
    color: var(--gold);
    margin-top: 1px;
  }
  .contact {
    margin-top: 18px;
    font-size: 12.8px;
    line-height: 18px;
    color: var(--text);
  }
  .contact b { color: var(--navy); font-weight: 500; }
  .contact .sep { color: var(--gold); padding: 0 4px; }
  .social {
    display: flex;
    gap: 4px;
    margin-top: 13px;
  }
  .social span {
    width: 19px;
    height: 19px;
    border: 1.5px solid var(--navy);
    border-radius: 50%;
  }
</style>
</head>
<body>
  <h1 class="showcase-title"><strong>CLICKABLE&nbsp; HTML</strong> EMAIL SIGNATURE</h1>

  <section class="signature signature--photo">
    <div class="portrait" role="img" aria-label="Portrait photo of the staff member"></div>
    <div class="divider"></div>
    <div class="details">
      <p class="person-name">NORA L. WHITFIELD</p>
      <p class="person-role">Founder &amp; CEO</p>
      <div class="contact">
        <p>48 Elm Avenue, Suite 4 Fairview, OH 44126</p>
        <p><b>p.</b> (555) 318-4072<span class="sep">|</span><b>m.</b> (555) 318-4072</p>
        <p><b>e.</b> hello@maplegrove.com<span class="sep">|</span><b>w.</b>www.maplegrove.com</p>
      </div>
      <div class="social"><span></span><span></span><span></span><span></span></div>
    </div>
  </section>

  <section class="signature signature--logo">
    <div class="brand-block">
      <div class="brand-dot"></div>
      <p class="brand-name">Maple Grove<br>Schools</p>
      <p class="brand-tagline">Growing Curious Minds Daily</p>
    </div>
    <div class="divider"></div>
    <div class="details">
      <p class="person-name">NORA L. WHITFIELD</p>
      <p class="person-role">Founder &amp; CEO</p>
      <div class="contact">
        <p>48 Elm Avenue, Suite 4 Fairview, OH 44126</p>
        <p><b>p.</b> (555) 318-4072<span class="sep">|</span><b>m.</b> (555) 318-4072</p>
        <p><b>e.</b> hello@maplegrove.com<span class="sep">|</span><b>w.</b>www.maplegrove.com</p>
      </div>
      <div class="social"><span></span><span></span><span></span><span></span></div>
    </div>
  </section>
</body>
</html>
```